Band and Coaching business card (creative industry)

My company The Fenwick Ensemble is the name of my band Soul outfit but is also a brand I use for my coaching business which is Performance coaching in the following areas: Corporate coaching, acting, vocals and dialect. The band plays for corporate events and private functions as well as local bar/restaurant/festivals.
Updates

Hi All

Please see updated info for the wording of the business card front and back.  This is ito then be followed with contact number, email and facebook link

first side should have:

JulieRose Brannigan
Creative Director
( followed by contact info as per previous)

Side 2:

The Fenwick Ensemble  - Band  
 Vocalist      I   Musician    I  Songwriter

The Fenwick Ensemble  - Studio
Performance Coaching  
Acting  I  Vocals  I Dialect  I Corporate Coaching

Industry/Entity Type

Events

Contact Information for Business Card

The Fenwick Ensemble (logo)
JulieRose Brannigan
Musician/Vocalist/Performance Coach
M: 0412 605 918
E: thefenwickensemble@mailbrook.net
W: www.friendspace.net/thefenwickensembleband

Font styles to use
Sans Serif

Requirements
Must have
• first side should have:

JulieRose Brannigan
Creative Director

Side 2:

The Fenwick Ensemble - Band
Vocalist I Musician I Songwriter

The Fenwick Ensemble - Studio
Performance Coaching
Acting I Vocals I Dialect I Corporate Coaching
Nice to have
• I like smaller business cards with curved edges.

some ideas for look in additional business cards attached.
Should not have
• music notes or anything specific to the field. Want to keep it funky and contemporary

```html
<!DOCTYPE html>
<html lang="en">
<head>
<meta charset="utf-8">
<title>The Fenwick Ensemble – Business Card</title>
<link rel="stylesheet" href="https://fonts.googleapis.com/css2?family=Oswald:wght@500&family=Open+Sans:wght@400&display=swap">
<style>
  :root {
    --stage: #dcdcdc;
    --card: #ffffff;
    --magenta: #cc4499;
    --purple: #7a3d9e;
    --name-purple: #6b3a98;
    --shadow: rgba(0, 0, 0, 0.14);
  }
  html, body {
    margin: 0;
    padding: 0;
    width: 1200px;
    height: 750px;
    overflow: hidden;
    background: var(--stage);
  }
  .canvas {
    position: relative;
    width: 1200px;
    height: 750px;
  }
  .card {
    position: absolute;
    top: 227px;
    width: 520px;
    height: 296px;
    border-radius: 28px;
    background: var(--card);
    box-shadow: 0 6px 18px var(--shadow);
    overflow: hidden;
  }
  .card--back { left: 50px; }
  .card--front { left: 630px; }

  .card-art {
    position: absolute;
    inset: 0;
    width: 100%;
    height: 100%;
  }

  .brand-mark {
    position: absolute;
    border-radius: 50%;
    background: var(--purple);
    display: flex;
    align-items: center;
    justify-content: center;
    text-align: center;
  }
  .brand-mark__name {
    font-family: "Oswald", sans-serif;
    font-weight: 500;
    line-height: 1.2;
    color: #ffffff;
    letter-spacing: 0.5px;
  }
  .card--back .brand-mark { left: 218px; top: 24px; width: 84px; height: 84px; }
  .card--back .brand-mark__name { font-size: 12px; }
  .card--front .brand-mark { left: 60px; top: 120px; width: 116px; height: 116px; }
  .card--front .brand-mark__name { font-size: 15px; }

  .services {
    position: absolute;
    left: 0;
    right: 0;
    top: 124px;
    text-align: center;
  }
  .service {
    margin: 0 0 14px;
  }
  .service__title {
    margin: 0 0 4px;
    font-family: "Oswald", sans-serif;
    font-weight: 500;
    font-size: 16px;
    line-height: 1.2;
    color: var(--name-purple);
  }
  .service__line {
    margin: 0;
    font-family: "Open Sans", sans-serif;
    font-size: 10px;
    line-height: 16px;
    color: var(--magenta);
    letter-spacing: 0.3px;
  }
  .service__divider {
    width: 60px;
    height: 1.5px;
    margin: 0 auto 12px;
    background: var(--magenta);
  }

  .holder {
    position: absolute;
    right: 30px;
    top: 34px;
    text-align: right;
  }
  .holder__name {
    margin: 0;
    font-family: "Oswald", sans-serif;
    font-weight: 500;
    font-size: 36px;
    line-height: 1;
    color: var(--name-purple);
  }
  .holder__title {
    margin: 6px 0 0;
    font-family: "Open Sans", sans-serif;
    font-size: 11px;
    color: var(--magenta);
    letter-spacing: 0.3px;
  }

  .contact {
    position: absolute;
    left: 222px;
    top: 170px;
    margin: 0;
    padding: 2px 0 2px 12px;
    list-style: none;
    border-left: 1.5px solid var(--magenta);
  }
  .contact__item {
    display: flex;
    align-items: center;
    gap: 7px;
    font-family: "Open Sans", sans-serif;
    font-size: 10px;
    line-height: 20px;
    color: var(--magenta);
  }
  .contact__icon {
    width: 10px;
    height: 10px;
    flex: none;
  }
</style>
</head>
<body>
<main class="canvas">

  <section class="card card--back" aria-label="Card back">
    <div class="brand-mark">
      <span class="brand-mark__name">The Fenwick<br>Ensemble</span>
    </div>

    <div class="services">
      <div class="service">
        <h2 class="service__title">The Fenwick Ensemble – Band</h2>
        <p class="service__line">Vocalist | Musician | Songwriter</p>
      </div>
      <div class="service__divider"></div>
      <div class="service">
        <h2 class="service__title">The Fenwick Ensemble – Studio</h2>
        <p class="service__line">Performance Coaching</p>
        <p class="service__line">Acting | Vocals | Dialect | Corporate Coaching</p>
      </div>
    </div>
  </section>

  <section class="card card--front" aria-label="Card front">
    <svg class="card-art" viewBox="0 0 520 296" aria-hidden="true">
      <rect width="520" height="296" fill="var(--magenta)"/>
      <circle cx="440" cy="-30" r="350" fill="var(--card)"/>
    </svg>

    <div class="brand-mark">
      <span class="brand-mark__name">The Fenwick<br>Ensemble</span>
    </div>

    <header class="holder">
      <h1 class="holder__name">JulieRose Brannigan</h1>
      <p class="holder__title">Creative Director</p>
    </header>

    <ul class="contact">
      <li class="contact__item">
        <svg class="contact__icon" viewBox="0 0 10 10" aria-hidden="true">
          <path d="M2 0.8 L3.6 2.6 L2.8 3.6 Q4 6 6.4 7.2 L7.4 6.4 L9.2 8 L8 9.4 Q3 8.6 0.6 2 Z" fill="var(--magenta)"/>
        </svg>
        <span>0412 605 918</span>
      </li>
      <li class="contact__item">
        <svg class="contact__icon" viewBox="0 0 10 10" aria-hidden="true">
          <rect x="0.5" y="2" width="9" height="6.4" fill="var(--magenta)"/>
          <path d="M0.8 2.3 L5 5.6 L9.2 2.3" fill="none" stroke="#fff" stroke-width="0.9"/>
        </svg>
        <span>thefenwickensemble@mailbrook.net</span>
      </li>
      <li class="contact__item">
        <svg class="contact__icon" viewBox="0 0 10 10" aria-hidden="true">
          <circle cx="5" cy="5" r="4.2" fill="none" stroke="var(--magenta)" stroke-width="1"/>
          <ellipse cx="5" cy="5" rx="1.8" ry="4.2" fill="none" stroke="var(--magenta)" stroke-width="0.8"/>
          <line x1="0.8" y1="5" x2="9.2" y2="5" stroke="var(--magenta)" stroke-width="0.8"/>
        </svg>
        <span>www.friendspace.net/thefenwickensembleband</span>
      </li>
    </ul>
  </section>

</main>
</body>
</html>
```